" Nossa empresa oferece diversos tipos de soluçoes na área de Gestao de Ativos para empresas do Setor Elétrico Brasileiro. Somos uma empresa Jovem com grandes ambiçoes. Apesar de pequenos, já temos na nossa carteira grandes empresas do setor e nosso objetivo agora é ampliar os serviços nas empresas em que já atuamos e conquistar novos clientes "

```html
<!DOCTYPE html>
<html lang="pt-BR">
<head>
<meta charset="utf-8">
<title>Voltara — Gestão de Ativos</title>
<link rel="stylesheet" href="https://fonts.googleapis.com/css2?family=Open+Sans:wght@400;600;700&family=Oswald:wght@500&display=swap">
<style>
:root{
  --blue:#1f6fc0;
  --blue-light:#3f8fda;
  --blue-dark:#16508f;
  --ink:#2b2f36;
  --dark:#262a30;
  --grey:#f1f2f4;
  --muted:#8a8f98;
  --white:#ffffff;
}
*{margin:0;padding:0;box-sizing:border-box}
html,body{width:1200px;height:1200px;overflow:hidden;background:var(--white);font-family:"Open Sans",Arial,sans-serif;color:var(--ink)}
.page{position:absolute;left:348px;top:0;width:504px;height:1198px;background:var(--white);overflow:hidden}
.topbar{height:34px;background:var(--dark);display:flex;align-items:center;padding:0 12px;gap:10px}
.brand{display:flex;align-items:center;gap:5px;color:var(--white);font-weight:700;font-size:15px}
.brand .dot{width:10px;height:10px;border-radius:50%;background:var(--blue-light)}
.nav{display:flex;gap:9px;margin-left:auto;font-size:5.5px;font-weight:600;color:#cfd3d9;letter-spacing:.3px}
.nav .active{color:var(--white);background:var(--blue);padding:3px 5px;margin:-3px 0}
.phone{font-size:6.5px;color:var(--white);font-weight:600;display:flex;align-items:center;gap:3px;margin-left:8px}
.hero{position:relative;height:247px;background:linear-gradient(110deg,#dfe6ee 0%,#b9c7d6 40%,#6d86a3 75%,#3e5878 100%)}
.hero-tag{position:absolute;left:38px;background:rgba(20,30,45,.78);color:var(--white);font-family:"Oswald",sans-serif;font-size:12.5px;letter-spacing:.6px;padding:4px 8px}
.hero-tag.one{top:146px}.hero-tag.two{top:180px}
.hero-arrows{position:absolute;left:42px;top:216px;color:var(--white);font-size:12px;line-height:12px;display:flex;gap:12px}
.hero-dots{position:absolute;left:236px;bottom:10px;display:flex;gap:3px}
.hero-dots i{width:4px;height:4px;border-radius:50%;background:rgba(255,255,255,.6)}
.hero-dots i:first-child{background:var(--white)}
.section-title{display:flex;align-items:center;justify-content:center;gap:5px;font-size:11px;font-weight:700;letter-spacing:.5px}
.section-title .ico{width:12px;height:12px;border-radius:50%;background:var(--blue)}
.section-title b{color:var(--blue)}
.about{padding-top:17px;height:132px}
.stats{display:flex;justify-content:center;gap:6px;margin-top:13px}
.stat{width:64px;height:52px;background:var(--grey);border:1px solid #e2e4e8;text-align:center;padding-top:6px}
.stat .num{color:var(--blue);font-weight:700;font-size:7px}
.stat .cap{font-size:4.4px;color:var(--muted);line-height:1.2;height:12px}
.stat svg{display:block;margin:2px auto 0}
.stat.wide{width:70px}
.services{height:211px;background:linear-gradient(180deg,var(--blue) 0%,var(--blue-light) 100%);color:var(--white);padding-top:14px}
.services .section-title{color:var(--white)}
.services .section-title .ico{background:var(--white)}
.services .section-title b{color:#dbe9f8}
.svc-grid{display:grid;grid-template-columns:repeat(3,128px);column-gap:16px;row-gap:30px;justify-content:center;margin-top:38px}
.svc{display:flex;gap:7px}
.svc svg{flex:none;margin-top:2px}
.svc h3{font-size:5.4px;font-weight:700;letter-spacing:.2px;margin-bottom:3px}
.svc p{font-size:5px;line-height:1.45;color:#e3eefa}
.team{height:192px;background:var(--dark);padding-top:16px}
.team .section-title{color:var(--white)}
.team-row{display:flex;justify-content:center;gap:6px;margin-top:18px}
.card{width:116px;background:var(--white);padding:4px}
.card .photo{height:100px;background:linear-gradient(160deg,#e9edf2 0%,#9fb0c4 60%,#4d5d72 100%)}
.card .cap{font-size:5px;color:var(--blue);padding:4px 1px 2px}
.card .cap span{color:var(--muted)}
.testimonials{position:relative;height:240px;background:linear-gradient(180deg,var(--blue-dark) 0%,var(--blue) 100%);color:var(--white);padding-top:14px;overflow:hidden}
.testimonials .section-title{color:var(--white);position:relative}
.tower{position:absolute;right:0;top:0;width:250px;height:240px;background:linear-gradient(90deg,rgba(31,111,192,0) 0%,rgba(120,175,230,.45) 45%,rgba(160,200,240,.75) 100%)}
.quote{position:absolute;left:66px;top:76px;width:372px;font-size:8.3px;line-height:1.4;text-align:center;quotes:none}
.quote .mark{position:absolute;left:-34px;top:-14px;font-size:30px;font-family:Georgia,serif}
.author{position:absolute;left:0;right:0;top:140px;display:flex;align-items:center;justify-content:center;gap:6px}
.author .avatar{width:18px;height:18px;border-radius:50%;background:linear-gradient(135deg,#e8c9a9,#8a5e43)}
.author .name{font-size:5.5px;font-weight:700;line-height:1.2}
.author .role{font-size:4.5px;line-height:1.25}
.t-arrow{position:absolute;top:84px;width:9px;height:9px;border-radius:50%;border:1px solid var(--white);font-size:6px;line-height:7px;text-align:center}
.t-arrow.l{left:8px}.t-arrow.r{right:8px}
.partners{position:absolute;left:0;right:0;top:204px;display:flex;justify-content:center;gap:6px}
.badge{width:42px;height:22px;background:var(--white);display:flex;align-items:center;justify-content:center}
.badge i{width:26px;height:10px;background:#c7ccd4;border-radius:2px}
.footer{height:108px;background:#f6f7f9;display:grid;grid-template-columns:90px 96px 110px 1fr;gap:12px;padding:12px 14px 0}
.footer h4{font-size:5px;font-weight:700;margin-bottom:3px}
.footer p{font-size:4.4px;color:var(--muted);line-height:1.4;margin-bottom:5px}
.contact{display:flex;gap:4px;align-items:flex-start;margin-bottom:7px}
.contact p{margin:0}
.field{height:9px;background:var(--white);border:1px solid #dfe2e6;margin-bottom:3px}
.field.area{height:22px}
.send{width:24px;height:8px;background:var(--blue);margin-left:auto}
.map{height:66px;background:linear-gradient(135deg,#e8ecef,#cfd8df)}
.bottombar{height:34px;background:var(--blue);display:flex;align-items:center;padding:0 14px}
.bottombar .brand{font-size:14px}
.bottombar .nav{color:#dbe9f8}
</style>
</head>
<body>
<main class="page">
  <header class="topbar">
    <div class="brand"><span class="dot"></span>Voltara</div>
    <nav class="nav">
      <span class="active">PÁGINA INICIAL</span><span>SOBRE NÓS</span><span>O QUE FAZEMOS</span><span>PARCEIROS</span><span>ATENDIMENTO</span>
    </nav>
    <div class="phone">
      <svg width="6" height="6" viewBox="0 0 10 10"><path d="M2 1l2 2-1 1.5c.7 1.3 1.3 2 2.5 2.5L7 6l2 2-1.5 1.5C4 9 1 6 .5 2.5z" fill="#fff"/></svg>
      (11) 4000-0000
    </div>
  </header>

  <section class="hero" role="img" aria-label="Foto de equipe de executivos em escritório">
    <div class="hero-tag one">SOLUÇÕES EM GESTÃO DE ATIVOS</div>
    <div class="hero-tag two">PARA EMPRESAS DO SETOR ELÉTRICO</div>
    <div class="hero-arrows"><span>‹</span><span>›</span></div>
    <div class="hero-dots"><i></i><i></i><i></i></div>
  </section>

  <section class="about">
    <h2 class="section-title"><span class="ico"></span><span><b>QUEM</b> SOMOS?</span></h2>
    <div class="stats">
      <div class="stat"><div class="num">+18</div><div class="cap">Projetos de<br>gestão entregues</div>
        <svg width="26" height="14" viewBox="0 0 26 14"><path d="M2 13a11 11 0 0 1 22 0" fill="none" stroke="#d3d7dd" stroke-width="3"/><path d="M2 13a11 11 0 0 1 17-9" fill="none" stroke="#1f6fc0" stroke-width="3"/></svg></div>
      <div class="stat"><div class="num">+30</div><div class="cap">FISCALIZAÇÕES</div>
        <svg width="26" height="14" viewBox="0 0 26 14"><path d="M2 13a11 11 0 0 1 22 0" fill="none" stroke="#d3d7dd" stroke-width="3"/><path d="M2 13a11 11 0 0 1 20-6" fill="none" stroke="#1f6fc0" stroke-width="3"/></svg></div>
      <div class="stat"><div class="num">+200</div><div class="cap">Laudos de<br>transformadores</div>
        <svg width="26" height="14" viewBox="0 0 26 14"><path d="M2 13a11 11 0 0 1 22 0" fill="none" stroke="#d3d7dd" stroke-width="3"/><path d="M2 13a11 11 0 0 1 22 0" fill="none" stroke="#1f6fc0" stroke-width="3"/></svg></div>
      <div class="stat wide"><div class="cap" style="height:18px">Referência em implantação<br>de gestão de ativos<br>no setor elétrico</div>
        <svg width="26" height="14" viewBox="0 0 26 14"><path d="M2 13a11 11 0 0 1 22 0" fill="none" stroke="#d3d7dd" stroke-width="3"/></svg></div>
    </div>
  </section>

  <section class="services">
    <h2 class="section-title"><span class="ico"></span><span>O QUE <b>FAZEMOS?</b></span></h2>
    <div class="svc-grid">
      <div class="svc"><svg width="13" height="13" viewBox="0 0 12 12"><circle cx="6" cy="6" r="3" fill="none" stroke="#fff" stroke-width="1.5"/><path d="M6 0v2M6 10v2M0 6h2M10 6h2M1.8 1.8l1.4 1.4M8.8 8.8l1.4 1.4M1.8 10.2l1.4-1.4M8.8 3.2l1.4-1.4" stroke="#fff" stroke-width="1.3"/></svg>
        <div><h3>GESTÃO DE ATIVOS ELÉTRICOS</h3><p>Soluções sob medida para aumentar a confiabilidade e a vida útil dos seus equipamentos em operação.</p></div></div>
      <div class="svc"><svg width="13" height="13" viewBox="0 0 12 12"><rect x="2" y="5" width="8" height="6" rx="1" fill="#fff"/><path d="M4 5V3.5a2 2 0 0 1 4 0V5" fill="none" stroke="#fff" stroke-width="1.2"/></svg>
        <div><h3>PLANOS DE MANUTENÇÃO</h3><p>Planejamento preventivo e preditivo alinhado às normas do setor e às metas da sua empresa.</p></div></div>
      <div class="svc"><svg width="13" height="13" viewBox="0 0 12 12"><circle cx="6" cy="5" r="3.5" fill="none" stroke="#fff" stroke-width="1.2"/><path d="M4.5 10h3" stroke="#fff" stroke-width="1.2"/></svg>
        <div><h3>CONSULTORIA TÉCNICA</h3><p>Apoio especializado na tomada de decisão sobre investimentos e expansão da rede elétrica.</p></div></div>
      <div class="svc"><svg width="13" height="13" viewBox="0 0 12 12"><path d="M1 11L11 1M7 1h4v4" fill="none" stroke="#fff" stroke-width="1.3"/></svg>
        <div><h3>INSPEÇÃO DE CAMPO</h3><p>Equipes qualificadas para vistorias em subestações, linhas e redes de distribuição.</p></div></div>
      <div class="svc"><svg width="13" height="13" viewBox="0 0 12 12"><circle cx="6" cy="3.5" r="2.3" fill="#fff"/><path d="M1.5 11a4.5 4.5 0 0 1 9 0z" fill="#fff"/></svg>
        <div><h3>TREINAMENTO DE EQUIPES</h3><p>Capacitação prática em metodologias modernas de gestão de ativos para o seu time.</p></div></div>
      <div class="svc"><svg width="13" height="13" viewBox="0 0 12 12"><path d="M1 11V7M4.5 11V5M8 11V3M11 11V1" stroke="#fff" stroke-width="1.6"/></svg>
        <div><h3>ANÁLISE DE DADOS</h3><p>Indicadores claros para priorizar intervenções, reduzir custos e evitar falhas.</p></div></div>
    </div>
  </section>

  <section class="team">
    <h2 class="section-title"><span class="ico"></span><span>EQUIPE <b style="color:#fff">QUALIFICADA</b></span></h2>
    <div class="team-row">
      <div class="card"><div class="photo" role="img" aria-label="Foto de colaborador"></div><div class="cap">Colaborador Nome <span>- Especialista</span></div></div>
      <div class="card"><div class="photo" role="img" aria-label="Foto de colaborador"></div><div class="cap">Colaborador Nome <span>- Engenheiro</span></div></div>
      <div class="card"><div class="photo" role="img" aria-label="Foto de colaborador"></div><div class="cap">Colaborador Nome <span>- Consultor</span></div></div>
      <div class="card"><div class="photo" role="img" aria-label="Foto de colaborador"></div><div class="cap">Colaborador Nome <span>- Analista</span></div></div>
    </div>
  </section>

  <section class="testimonials">
    <div class="tower" role="img" aria-label="Foto de edifício corporativo espelhado"></div>
    <h2 class="section-title"><span class="ico" style="background:#fff"></span><span>NOSSOS <b style="color:#dbe9f8">CLIENTES</b></span></h2>
    <span class="t-arrow l">‹</span><span class="t-arrow r">›</span>
    <blockquote class="quote"><span class="mark">“</span>But I must explain to you how all this mistaken idea of denouncing pleasure and praising pain was born and I will give you a complete account of the system, and expound the actual teachings of the great.</blockquote>
    <div class="author">
      <div class="avatar" role="img" aria-label="Foto da cliente"></div>
      <div><div class="name">Clara Duarte</div><div class="role">Cargo<br>Empresa</div></div>
    </div>
    <div class="partners">
      <div class="badge"><i></i></div><div class="badge"><i></i></div><div class="badge"><i></i></div>
      <div class="badge"><i></i></div><div class="badge"><i></i></div><div class="badge"><i></i></div>
    </div>
  </section>

  <footer class="footer">
    <div>
      <h4>VOLTARA SOLUÇÕES</h4>
      <p>Empresa jovem com grandes ambições, dedicada à gestão de ativos do setor elétrico brasileiro.</p>
      <h4 style="color:var(--blue)">ENDEREÇO</h4>
      <p>Rua das Palmeiras, 120<br>Centro — Cidade Nova</p>
    </div>
    <div style="padding-top:6px">
      <div class="contact"><svg width="8" height="8" viewBox="0 0 10 10"><circle cx="5" cy="5" r="5" fill="#1f6fc0"/></svg><p><b>TELEFONE</b><br>(11) 4000-0000</p></div>
      <div class="contact"><svg width="8" height="8" viewBox="0 0 10 10"><circle cx="5" cy="5" r="5" fill="#1f6fc0"/></svg><p><b>E-MAIL</b><br>contato@voltara.exemplo</p></div>
      <div class="contact"><svg width="8" height="8" viewBox="0 0 10 10"><circle cx="5" cy="5" r="5" fill="#1f6fc0"/></svg><p><b>SITE</b><br>www.voltara.exemplo</p></div>
    </div>
    <form>
      <div class="field"></div><div class="field"></div><div class="field area"></div><div class="send"></div>
    </form>
    <div class="map" role="img" aria-label="Mapa de localização do escritório"></div>
  </footer>

  <div class="bottombar">
    <div class="brand"><span class="dot" style="background:#fff"></span>Voltara</div>
    <nav class="nav"><span>PÁGINA INICIAL</span><span>SOBRE NÓS</span><span>O QUE FAZEMOS</span><span>PARCEIROS</span><span>ATENDIMENTO</span></nav>
  </div>
</main>
</body>
</html>
```